Business Cards for new orthopaedic surgery practice

My husband and I are starting our own orthopaedic surgery practice. We are looking for a business card that is uniform, but one will have my name/title and the other will have his. You can just create one design with my name on it for now. But when I choose your design as the winning design I will ask that you add another copy with his name/title.

We are looking for classy, simple, elite all in one. We like dark blues/a little gold/yellow. Something that goes with our logo. We want our logo incorporated. Here is all the info you need:
Business name: RV Bone & Vitality Center
Location: 38517 North Willowmere Ave
Palm Hollow, FL 33990
Phone: 954-218-4063
Fax: 954-582-7341
Email: info@myrvbonecare.example

Names: Lydia Vance, M.D.
Board Certified Hand and Upper Extremity Surgeon

Ebo Dansu, M.D.
Board Certified Hip & Knee Replacement/General Orthopaedic Surgeon

Can decide what you want to put on the back. Maybe a slogan:
Grounded in Care. Centered on You

I am just going to upload our logo. The only thing is if we select you as the winning design, the location, and phone numbers may change. We will need your help to update that once fully solidified.

Industry/Entity Type

Medical

Contact Information for Business Card

Colors
0054AA
0677BA
7BADD7
CADEEF
E8F1F8
0094D4
00A9DD
6FCCEA
C7EBF8
E9F6FB

Requirements
Must have
• class, appeal,
Should not have
• We want to air on the side of masculine if we are looking at masculine vs. feminine feel. But we still want it classy, sophisticated, and something we will love

```html
<!DOCTYPE html>
<html lang="en">
<head>
<meta charset="utf-8">
<title>RV Bone &amp; Vitality Center — Business Card</title>
<link href="https://fonts.googleapis.com/css2?family=Poppins:wght@400;500;600&display=swap" rel="stylesheet">
<style>
  :root {
    --stage: #1b1c1f;
    --card-blue: #263f86;
    --accent-cyan: #1fb3e3;
    --ink-white: #ffffff;
    --rule-cyan: #22b5e6;
  }
  html, body {
    margin: 0;
    width: 1200px;
    height: 900px;
    overflow: hidden;
    background: var(--stage);
    font-family: "Poppins", sans-serif;
  }
  .stage {
    width: 1200px;
    height: 900px;
    display: flex;
    flex-direction: column;
    align-items: center;
    justify-content: center;
    gap: 36px;
  }
  .card {
    position: relative;
    width: 700px;
    height: 400px;
    background: var(--card-blue);
    color: var(--ink-white);
    overflow: hidden;
    box-shadow: 0 10px 30px rgba(0,0,0,.5);
  }
  .brand {
    display: flex;
    align-items: center;
    gap: 14px;
  }
  .brand-mark {
    width: 22px;
    height: 22px;
    border-radius: 50%;
    background: var(--ink-white);
    flex: none;
  }
  .brand-name {
    font-weight: 600;
    color: var(--ink-white);
    text-transform: uppercase;
    letter-spacing: 1px;
    line-height: 1.15;
  }

  /* front */
  .card-front .brand { position: absolute; left: 130px; top: 52px; }
  .card-front .brand-name { font-size: 22px; width: 200px; }
  .contact-list {
    position: absolute;
    left: 60px;
    top: 200px;
    margin: 0;
    padding: 0;
    list-style: none;
    font-size: 14px;
    line-height: 1.6;
  }
  .contact-list li { display: flex; align-items: center; gap: 8px; }
  .contact-list svg { width: 13px; height: 13px; fill: var(--ink-white); flex: none; }
  .person {
    position: absolute;
    right: 60px;
    top: 178px;
    text-align: right;
  }
  .person-name {
    margin: 0;
    font-size: 22px;
    font-weight: 600;
    color: var(--accent-cyan);
    letter-spacing: .5px;
  }
  .person-title {
    margin: 4px 0 0;
    font-size: 15px;
    font-weight: 400;
  }
  .edge-tab {
    position: absolute;
    right: 0;
    top: 236px;
    width: 28px;
    height: 42px;
    background: var(--accent-cyan);
  }

  /* back */
  .card-back {
    display: flex;
    flex-direction: column;
    align-items: center;
    justify-content: center;
  }
  .card-back .brand-name { font-size: 32px; width: 360px; }
  .card-back .brand-mark { width: 30px; height: 30px; }
  .tagline {
    margin: 30px 0 0;
    padding: 8px 24px;
    border-top: 2px solid var(--rule-cyan);
    border-bottom: 2px solid var(--rule-cyan);
    font-size: 18px;
    letter-spacing: .5px;
  }
</style>
</head>
<body>
<main class="stage">

  <section class="card card-front" aria-label="Business card front">
    <div class="brand">
      <span class="brand-mark"></span>
      <span class="brand-name">RV Bone &amp; Vitality Center</span>
    </div>

    <ul class="contact-list">
      <li>
        <svg viewBox="0 0 24 24" aria-hidden="true"><path d="M6.6 10.8a15.1 15.1 0 0 0 6.6 6.6l2.2-2.2a1 1 0 0 1 1-.25 11.4 11.4 0 0 0 3.6.57 1 1 0 0 1 1 1V20a1 1 0 0 1-1 1A17 17 0 0 1 3 4a1 1 0 0 1 1-1h3.5a1 1 0 0 1 1 1c0 1.25.2 2.45.57 3.57a1 1 0 0 1-.25 1z"/></svg>
        954-218-4063
      </li>
      <li>
        <svg viewBox="0 0 24 24" aria-hidden="true"><path d="M6 3h10v5H6zM4 9h16a2 2 0 0 1 2 2v7h-4v3H6v-3H2v-7a2 2 0 0 1 2-2zm4 7v3h8v-3z"/></svg>
        954-582-7341
      </li>
      <li>
        <svg viewBox="0 0 24 24" aria-hidden="true"><path d="M3 5h18v14H3zm2 2v.5l7 4.5 7-4.5V7z"/></svg>
        info@myrvbonecare.example
      </li>
      <li>38517 North Willowmere Ave</li>
      <li>Palm Hollow, FL 33990</li>
    </ul>

    <div class="person">
      <h1 class="person-name">Lydia Vance, M.D.</h1>
      <p class="person-title">Hand and Upper Extremity Surgery</p>
    </div>
    <span class="edge-tab"></span>
  </section>

  <section class="card card-back" aria-label="Business card back">
    <div class="brand">
      <span class="brand-mark"></span>
      <span class="brand-name">RV Bone &amp; Vitality Center</span>
    </div>
    <p class="tagline">Grounded in Care. Centered on You</p>
  </section>

</main>
</body>
</html>
```